Seeking a new website design for electrical contracting company

Brisket & Vane electrical contracting needs a new website for brisket-vane.example

We are looking for modern and something real cool with motion for a landing page. we have some cool images from our photo shoot. maybe even 3d motion our existing logo. we would like something we can edit with news and events and update a past project page. Also allow to take payment
stock images at
https://lorapellwinphotos.picvault-demo.example/Brisket-and-Vane

Target Market(s)

construction , home owners , business owners,

Industry/Entity Type

construction , electrical

Coding

Number of Pages Required

5+ page

Font styles to use
Serif
Sans Serif

Colors
0054AA
0677BA
7BADD7
CADEEF
E8F1F8
0094D4
00A9DD
6FCCEA
C7EBF8
E9F6FB
FFF300
FFF600
FEFA6F
FFFEC7
FFFEE8

Requirements
Must have
• excitement, motion, selling professionalism,

```html
<!DOCTYPE html>
<html lang="en">
<head>
<meta charset="utf-8">
<title>Brisket &amp; Vane Electrical Contractors</title>
<link href="https://fonts.googleapis.com/css2?family=Lato:ital,wght@0,400;0,700;0,900;1,700&display=swap" rel="stylesheet">
<style>
:root{
  --navy:#2A3778;
  --navy-deep:#243170;
  --orange:#F7A21B;
  --orange-edge:#D9860A;
  --ink:#2E2E2E;
  --muted:#555;
  --lavender:#EEF0FB;
  --white:#fff;
}
*{margin:0;padding:0;box-sizing:border-box}
html,body{width:1200px;height:3158px;overflow:hidden}
body{position:relative;background:var(--white);font-family:'Lato',sans-serif;color:var(--ink)}
.abs{position:absolute}
.btn{position:absolute;display:flex;align-items:center;justify-content:center;background:var(--orange);border:2px solid var(--orange-edge);color:var(--white);font-size:20px;font-weight:700;text-decoration:none}
.brand{position:absolute;display:flex;align-items:center;gap:10px}
.brand-dot{width:44px;height:44px;border-radius:50%;background:var(--navy)}
.brand-name{font-size:27px;font-weight:900;color:var(--navy);letter-spacing:.5px}
.nav{position:absolute;top:31px;font-size:16px;color:var(--ink)}
.nav.active{color:var(--navy)}
.hero-title{position:absolute;left:108px;top:210px;font-size:54px;font-weight:700;line-height:60px;color:var(--navy)}
.h2{position:absolute;left:0;width:1200px;text-align:center;font-size:44px;font-weight:700;color:var(--navy)}
.h2 .accent,.about-title .accent{color:var(--orange)}
.about-title{position:absolute;left:642px;top:682px;font-size:40px;font-weight:700;color:var(--navy)}
.about-list{position:absolute;left:642px;top:746px;width:445px;list-style:none;font-size:15.5px;line-height:28.2px;color:var(--ink)}
.about-list li{position:relative;padding-left:25px}
.about-list svg{position:absolute;left:0;top:7px}
.projects{position:absolute;left:0;top:1123px;width:1200px;height:554px;background:var(--navy)}
.project{position:absolute;top:155px;width:410px;color:var(--white)}
.project h3{font-size:34px;font-weight:700;margin-top:100px;margin-bottom:10px}
.project p{font-size:16px;line-height:27.5px;height:137px;overflow:hidden}
.project .more{display:block;margin-top:10px;font-size:20px;font-weight:700;font-style:italic;color:var(--white)}
.service{position:absolute;top:1825px;width:308px}
.service .photo{height:292px;border-radius:6px;box-shadow:0 2px 6px rgba(0,0,0,.25)}
.service h4{text-align:center;font-size:23px;font-weight:700;margin-top:22px;color:var(--ink);white-space:nowrap}
.arrow{position:absolute}
.scenes-bg{position:absolute;left:0;top:2243px;width:1200px;height:600px}
.post{position:absolute;top:2380px;width:308px;height:299px;background:var(--white);box-shadow:0 2px 8px rgba(0,0,0,.18)}
.post .photo{height:151px}
.post .body{padding:14px 17px 0}
.post h5{font-size:16.5px;font-weight:700;color:var(--ink)}
.post .meta{display:flex;justify-content:space-between;font-size:13px;color:var(--muted);margin-top:6px;padding-right:15px}
.post p{font-size:13.5px;line-height:22px;height:44px;overflow:hidden;margin-top:6px;color:var(--ink)}
.post .more{display:block;font-size:18px;font-weight:700;font-style:italic;color:var(--ink);margin-top:3px}
.foot-title{position:absolute;font-size:21px;font-weight:700;color:var(--navy)}
.quick{position:absolute;left:223px;top:2921px;list-style:none;font-size:16px;line-height:28.2px}
.quick li{display:flex;align-items:center;gap:11px}
.quick li::before{content:"";width:8px;height:8px;background:var(--navy)}
.social{position:absolute;top:2982px;width:28px;height:28px;border-radius:50%;background:var(--navy-deep)}
.contact-row{position:absolute;left:836px;display:flex;align-items:center;gap:9px;font-size:15.5px}
.contact-addr{position:absolute;left:870px;top:3003px;font-size:15.5px;line-height:28px}
.divider{position:absolute;left:110px;top:3103px;width:981px;height:1px;background:#ccc}
.copy{position:absolute;left:0;top:3118px;width:1200px;text-align:center;font-size:15px}
</style>
</head>
<body>

<header>
  <div class="brand" style="left:80px;top:21px">
    <span class="brand-dot"></span><span class="brand-name">BRISKET &amp; VANE</span>
  </div>
  <nav>
    <a class="nav active" style="left:428px">Home</a>
    <a class="nav" style="left:491px">About</a>
    <a class="nav" style="left:559px">Services</a>
    <a class="nav" style="left:639px">Project</a>
    <a class="nav" style="left:711px">Testimonials</a>
    <a class="nav" style="left:819px">Blog</a>
  </nav>
  <a class="btn" style="left:919px;top:20px;width:169px;height:46px">Contact Us</a>
</header>

<section class="hero">
  <svg class="abs" style="left:0;top:86px" width="1200" height="530" viewBox="0 86 1200 530">
    <defs>
      <linearGradient id="heroFill" x1="0" y1="0" x2="1" y2="0.4">
        <stop offset="0" stop-color="#5C7FA6"/>
        <stop offset="0.3" stop-color="#BFE3F2"/>
        <stop offset="0.55" stop-color="#4FA6D6"/>
        <stop offset="0.8" stop-color="#2C7DB4"/>
        <stop offset="1" stop-color="#D97A35"/>
      </linearGradient>
    </defs>
    <polygon role="img" aria-label="Photo of two electricians in hard hats and vests looking at a site, with glowing technology icons" points="0,86 1200,86 1200,538 600,585 0,535" fill="url(#heroFill)"/>
    <polygon points="0,535 600,585 1200,538 1200,552 600,609 0,552" fill="var(--navy)"/>
  </svg>
  <h1 class="hero-title">Born from the Lens.<br>Brought to Life.</h1>
  <a class="btn" style="left:112px;top:352px;width:169px;height:46px">Contact Us</a>
</section>

<section class="about">
  <svg class="abs" style="left:100px;top:605px" width="475" height="495" viewBox="100 605 475 495">
    <defs>
      <linearGradient id="aboutFill" x1="0" y1="0" x2="1" y2="1">
        <stop offset="0" stop-color="#C9532A"/>
        <stop offset="0.45" stop-color="#3D434C"/>
        <stop offset="1" stop-color="#1E2228"/>
      </linearGradient>
    </defs>
    <polygon points="336,612 563,735 563,965 336,1090 110,965 110,735" fill="none" stroke="var(--orange)" stroke-width="2"/>
    <polygon role="img" aria-label="Photo of an electrician in an orange hard hat working on a wiring panel" points="333,628 548,748 548,955 333,1075 122,955 122,748" fill="url(#aboutFill)"/>
  </svg>
  <h2 class="about-title">About <span class="accent">Us</span></h2>
  <ul class="about-list">
    <li><svg width="17" height="17" viewBox="0 0 17 17"><circle cx="8.5" cy="8.5" r="7.5" fill="none" stroke="#333" stroke-width="1.2"/><path d="M5 8.5h6M8.5 6l2.5 2.5-2.5 2.5" fill="none" stroke="#333" stroke-width="1.2"/></svg>We’re a creative team that lives at the intersection of design, motion, and storytelling. From the first sketch to the final scroll animation, we craft digital experiences that connect, excite, and stay with you.</li>
    <li><svg width="17" height="17" viewBox="0 0 17 17"><circle cx="8.5" cy="8.5" r="7.5" fill="none" stroke="#333" stroke-width="1.2"/><path d="M5 8.5h6M8.5 6l2.5 2.5-2.5 2.5" fill="none" stroke="#333" stroke-width="1.2"/></svg>Whether it’s a bold landing page, a cinematic brand moment, or a 3D logo that turns heads — we make work that moves. Literally.</li>
  </ul>
  <a class="btn" style="left:642px;top:968px;width:169px;height:47px">Contact Us</a>
</section>

<section class="projects">
  <h2 class="h2" style="top:72px;color:var(--white)">Our Project</h2>
  <div class="project" style="left:110px">
    <svg class="abs" style="left:2px;top:0" width="80" height="78" viewBox="0 0 80 78" fill="none" stroke="#fff" stroke-width="2.5">
      <rect x="2" y="2" width="76" height="55" rx="3"/>
      <path d="M32 57v10M48 57v10M22 70h36"/>
      <path d="M8 32h14l5-12 7 22 6-16 5 8 6-4h21"/>
      <circle cx="40" cy="28" r="6"/>
    </svg>
    <h3>Brightwave Studios</h3>
    <p>We partnered with Brightwave to launch their new identity with a high-energy digital experience. Centered around motion and vibe, the site featured scroll-triggered animation, a 3D logo reveal, and embedded cinematic visuals from their latest campaign. Built to leave a lasting impression.</p>
    <a class="more">Read More..</a>
  </div>
  <svg class="abs" style="left:536px;top:158px" width="120" height="310" viewBox="0 0 120 310">
    <defs>
      <linearGradient id="boltFill" x1="0" y1="0" x2="0" y2="1">
        <stop offset="0" stop-color="#F7A21B"/><stop offset="1" stop-color="#F39A12"/>
      </linearGradient>
    </defs>
    <rect role="img" aria-label="Orange lightning bolt accent" x="40" y="0" width="40" height="310" rx="20" fill="url(#boltFill)"/>
  </svg>
  <div class="project" style="left:694px">
    <svg class="abs" style="left:0;top:0" width="80" height="78" viewBox="0 0 80 78" fill="none" stroke="#fff" stroke-width="2.5">
      <rect x="2" y="2" width="16" height="16" rx="2"/>
      <rect x="62" y="22" width="16" height="16" rx="2"/>
      <rect x="2" y="40" width="16" height="16" rx="2"/>
      <rect x="62" y="60" width="16" height="16" rx="2"/>
      <path d="M18 10h40v12M54 18l4 4 4-4M18 48h16M46 48h16M50 68H24M28 64l-4 4 4 4"/>
      <circle cx="40" cy="42" r="7"/>
    </svg>
    <h3>Studio Marrow</h3>
    <p>For Kestrel Form’s rebrand, we designed a sleek, CMS-driven portfolio that lets them update their projects, news, and team with ease. The site includes smooth transitions, dynamic content filtering, and subtle motion that brings their aesthetic to life.</p>
    <a class="more">Read More..</a>
  </div>
</section>

<section class="services">
  <h2 class="h2" style="top:1752px">Our <span class="accent">Services</span></h2>
  <svg class="arrow" style="left:46px;top:1967px" width="14" height="22" viewBox="0 0 14 22"><path d="M12 2 3 11l9 9" fill="none" stroke="#444" stroke-width="2.5"/></svg>
  <svg class="arrow" style="left:1134px;top:1967px" width="14" height="22" viewBox="0 0 14 22"><path d="M2 2l9 9-9 9" fill="none" stroke="#444" stroke-width="2.5"/></svg>
  <div class="service" style="left:110px">
    <div class="photo" role="img" aria-label="Photo of hands holding printed website wireframes at a desk" style="background:linear-gradient(135deg,#E6E4E0,#C9C4BC 55%,#6F6A66)"></div>
    <h4>Web Design &amp; Development</h4>
  </div>
  <div class="service" style="left:451px">
    <div class="photo" role="img" aria-label="Photo of a designer working on 3D animation software at a monitor" style="background:linear-gradient(160deg,#8A8F8E,#3F4545 50%,#1F2425)"></div>
    <h4>Motion Design &amp; 3D Animation</h4>
  </div>
  <div class="service" style="left:780px">
    <div class="photo" role="img" aria-label="Double exposure photo of a profile silhouette over a city at sunset" style="background:linear-gradient(90deg,#26505A,#4E6A6C 45%,#C7623A 80%,#E08A4E)"></div>
    <h4>Branding &amp; Visual Identity</h4>
  </div>
</section>

<section class="scenes">
  <svg class="scenes-bg" width="1200" height="600" viewBox="0 2243 1200 600">
    <polygon points="0,2243 1200,2243 1200,2831 600,2768 0,2831" fill="var(--lavender)"/>
    <polyline points="0,2831 600,2768 1200,2831" fill="none" stroke="var(--navy)" stroke-width="8"/>
  </svg>
  <h2 class="h2" style="top:2312px">Behind the <span class="accent">Scenes</span></h2>
  <svg class="arrow" style="left:46px;top:2500px" width="14" height="22" viewBox="0 0 14 22"><path d="M12 2 3 11l9 9" fill="none" stroke="#444" stroke-width="2.5"/></svg>
  <svg class="arrow" style="left:1134px;top:2500px" width="14" height="22" viewBox="0 0 14 22"><path d="M2 2l9 9-9 9" fill="none" stroke="#444" stroke-width="2.5"/></svg>
  <article class="post" style="left:113px">
    <div class="photo" role="img" aria-label="Photo of two colleagues discussing work at a glass board in an office" style="background:linear-gradient(90deg,#C9D7E3,#8FA4B8 50%,#5A5048)"></div>
    <div class="body">
      <h5>Animating a Logo in 3D: Our Workflow</h5>
      <div class="meta"><span>April 5, 2025</span><span>Motion Design</span></div>
      <p>A quick breakdown of how we bring static logos to life using 3D tools and motion design.</p>
      <a class="more">Read more..</a>
    </div>
  </article>
  <article class="post" style="left:447px">
    <div class="photo" role="img" aria-label="Photo of glowing red electrical sparks across dark equipment" style="background:linear-gradient(90deg,#2B2F3A,#7A2A22 40%,#2A2E38 75%,#1D2029)"></div>
    <div class="body">
      <h5>Visual Direction for Brightwave</h5>
      <div class="meta"><span>March 2, 2025</span><span>Projects</span></div>
      <p>Breaking down the creative choices, moodboarding, and motion for one of our favourite launches.</p>
      <a class="more">Read more..</a>
    </div>
  </article>
  <article class="post" style="left:781px">
    <div class="photo" role="img" aria-label="Photo of hands reviewing plans spread on a table" style="background:linear-gradient(90deg,#3C4A56,#8D8478 50%,#C9BBA6)"></div>
    <div class="body">
      <h5>Tools We’re Loving in 2025</h5>
      <div class="meta"><span>January 28, 2025</span><span>Tools &amp; Tech</span></div>
      <p>From Kinetix Motion to Shapeloom and Pagewright, here are the tools in our daily design and dev kit.</p>
      <a class="more">Read more..</a>
    </div>
  </article>
</section>

<footer>
  <h3 class="foot-title" style="left:223px;top:2880px">Quick Links</h3>
  <ul class="quick">
    <li>Home</li><li>About</li><li>Project</li><li>Services</li><li>Blog</li>
  </ul>
  <div class="brand" style="left:466px;top:2888px">
    <span class="brand-dot"></span><span class="brand-name">BRISKET &amp; VANE</span>
  </div>
  <span class="social" style="left:502px" aria-label="Social profile"></span>
  <span class="social" style="left:547px" aria-label="Social profile"></span>
  <span class="social" style="left:592px" aria-label="Social profile"></span>
  <span class="social" style="left:634px" aria-label="Social profile"></span>

  <h3 class="foot-title" style="left:836px;top:2881px">Contact Us</h3>
  <div class="contact-row" style="top:2918px">
    <svg width="28" height="28" viewBox="0 0 28 28"><circle cx="14" cy="14" r="14" fill="var(--navy)"/><path d="M9.5 8.5c1-1 2-1 2.6 0l1.2 2c.4.7.2 1.3-.4 1.8l-.7.6c.8 1.7 2 2.9 3.7 3.7l.6-.7c.5-.6 1.1-.8 1.8-.4l2 1.2c1 .6 1 1.6 0 2.6-1.4 1.4-3.4 1-6-1.3-2.6-2.4-4.1-4.6-4.2-6.4-.1-1 .4-1.9 1-2.4z" fill="#fff"/></svg>
    <span>555 010 20</span>
  </div>
  <div class="contact-row" style="top:2957px">
    <svg width="28" height="28" viewBox="0 0 28 28"><circle cx="14" cy="14" r="14" fill="var(--navy)"/><rect x="7.5" y="9.5" width="13" height="9" rx="1" fill="none" stroke="#fff" stroke-width="1.5"/><path d="M7.5 10l6.5 5 6.5-5" fill="none" stroke="#fff" stroke-width="1.5"/></svg>
    <span>milo@brisket-vane.example</span>
  </div>
  <div class="contact-row" style="top:2999px">
    <svg width="28" height="28" viewBox="0 0 28 28"><circle cx="14" cy="14" r="14" fill="var(--navy)"/><path d="M14 6.5a5 5 0 0 0-5 5c0 3.8 5 9.5 5 9.5s5-5.7 5-9.5a5 5 0 0 0-5-5z" fill="#fff"/><circle cx="14" cy="11.5" r="2" fill="var(--navy)"/></svg>
  </div>
  <div class="contact-addr">BRISKET &amp; VANE<br>ELECTRICAL CONTRACTORS<br>Milo Brisket 1-555-010-4477</div>

  <div class="divider"></div>
  <p class="copy">Copyright © 2025. Brisket &amp; Vane electrical contracting. All Rights Reserved</p>
</footer>

</body>
</html>
```